Consulting company business cards

We have a base design, but would be willing to update. We have a new logo/"tag" that needs to be added. Current business card design is attached for reference into our "style."

Industry/Entity Type

Business

Contact Information for Business Card

Should contain name and title, office number, mobile number if appropriate, e-mail, website, physical address, and company logo.

Font styles to use
Other font styles liked:
• See current card design on KorvandBCard

Colors
0455a3
85acd3
aaaaaa

Requirements
Must have
• Our colors are navy blue, gray, and a lighter blue
Nice to have
• Design that I can easily drop in new names/titles as we hire employees.

```html
<!DOCTYPE html>
<html lang="en">
<head>
<meta charset="utf-8">
<title>Brenwick Business Cards</title>
<link rel="stylesheet" href="https://fonts.googleapis.com/css2?family=Open+Sans:wght@400;600;700&family=Roboto+Condensed:wght@700&display=swap">
<style>
  :root {
    --backdrop: #262626;
    --card-white: #ffffff;
    --navy: #0b3050;
    --navy-deep: #03304f;
    --light-blue: #7fb0cf;
    --text-grey: #444444;
    --tag-grey: #8a8a8a;
    --faint-blue: #e9f0f4;
  }
  * { margin: 0; padding: 0; box-sizing: border-box; }
  html, body {
    width: 1200px;
    height: 987px;
    overflow: hidden;
    background: var(--backdrop);
  }
  .stage {
    position: relative;
    width: 1200px;
    height: 987px;
  }
  .card {
    position: absolute;
    left: 293px;
    width: 615px;
    height: 351px;
    border-radius: 21px;
    overflow: hidden;
  }
  .card--front { top: 125px; background: var(--card-white); }
  .card--back { top: 510px; background: var(--navy-deep); }

  .brand-backdrop {
    position: absolute;
    right: 0;
    top: 0;
    width: 365px;
    height: 351px;
    background: radial-gradient(ellipse at 60% 45%, var(--faint-blue) 0%, var(--faint-blue) 45%, rgba(233,240,244,0) 75%);
  }

  .wordmark {
    position: absolute;
    left: 36px;
    top: 40px;
    display: flex;
    align-items: center;
    gap: 10px;
    font-family: "Roboto Condensed", "Arial Narrow", sans-serif;
    font-weight: 700;
    font-size: 52px;
    line-height: 1;
    letter-spacing: 2px;
    color: var(--navy);
  }
  .wordmark__dot {
    width: 30px;
    height: 30px;
    border-radius: 50%;
    background: var(--light-blue);
  }
  .tagline {
    position: absolute;
    left: 37px;
    top: 100px;
    font-family: "Open Sans", Arial, sans-serif;
    font-size: 11px;
    letter-spacing: 1.6px;
    color: var(--tag-grey);
    text-transform: uppercase;
  }
  .person__name {
    position: absolute;
    left: 36px;
    top: 123px;
    font-family: "Open Sans", Arial, sans-serif;
    font-weight: 700;
    font-size: 21px;
    color: var(--navy);
  }
  .person__title {
    position: absolute;
    left: 36px;
    top: 152px;
    font-family: "Open Sans", Arial, sans-serif;
    font-size: 17px;
    color: var(--light-blue);
  }
  .contact {
    position: absolute;
    left: 37px;
    font-family: "Open Sans", Arial, sans-serif;
    font-size: 15px;
    line-height: 21px;
    color: var(--text-grey);
  }
  .contact--address { top: 180px; }
  .contact--lines { top: 230px; }

  .back-mark {
    position: absolute;
    left: 0;
    right: 0;
    top: 128px;
    display: flex;
    justify-content: center;
    align-items: center;
    gap: 12px;
    font-family: "Roboto Condensed", "Arial Narrow", sans-serif;
    font-weight: 700;
    font-size: 58px;
    line-height: 1;
    letter-spacing: 3px;
    color: var(--light-blue);
  }
  .back-mark__dot {
    width: 34px;
    height: 34px;
    border-radius: 50%;
    background: var(--light-blue);
  }
  .back-url {
    position: absolute;
    left: 0;
    right: 0;
    top: 292px;
    text-align: center;
    font-family: "Open Sans", Arial, sans-serif;
    font-size: 16px;
    letter-spacing: 3.4px;
    color: var(--card-white);
  }
</style>
</head>
<body>
<main class="stage">
  <section class="card card--front">
    <div class="brand-backdrop" role="img" aria-label="Faint brand decoration area"></div>
    <div class="wordmark">BRENWICK<span class="wordmark__dot"></span></div>
    <p class="tagline">A Cloud Consulting Company</p>
    <h1 class="person__name">Jolenekorvand</h1>
    <p class="person__title">Office Manager</p>
    <p class="contact contact--address">1185 N Larkspur AVE<br>Marlow Ohio 45391</p>
    <p class="contact contact--lines">O 555.014.2210<br>F 555.014.2271<br>jkorvand@brenwicktech.com<br>www.brenwicktech.com</p>
  </section>

  <section class="card card--back">
    <div class="back-mark">BRENWICK<span class="back-mark__dot"></span></div>
    <p class="back-url">www.brenwicktech.com</p>
  </section>
</main>
</body>
</html>
```